International Clinical Software Company needs a new business card design

We are looking for a new business card design for our company that has recently expanded into the UK market, making us a multinational company.
After having rebranded our website and produced a new style guide, we are looking for a business card that is creative and attention grabbing, while being consistent with the style and colour scheme used on the new website, www.plumvora.example
We produce care management technology for the aged care market, but the main aspect we aim to communicate is the human element of our software, and the way it assists in providing better care for aged people, and stronger relationships between aged people and the staff that care for them.
Our current business card is a dark green with gold text, which makes the text quite difficult to read, not very aesthetically appealing and the colour scheme looks quite dated.
We would like something fresh and modern, that can still be colourful but doesn't use large blocks of dark colour, and uses the colours within our logo.
Something tying in with the leaves that are used in our logo could work quite nicely, along with the Autumn/Fall colours of soft greens, yellows and reds (also in our existing logo). However also happy to look at fresh, completely out of the box ideas we may not have yet considered.
Target Market(s)
The people that receive this business card work in the aged card or health industry and are either corporate/management level staff or clinical (Registered Nurses, care workers etc.)
Industry/Entity Type
Health Product
Contact Information for Business Card
Company Name - BrindlewayCare
Company locations: United Kingdom, Australia, New Zealand
Staff Details:
Staff name: Derek Mallow
Staff job title: Executive Chairman
Staff email: d.mallow@plumvora.example
Office phone number: 01742 918576
Font styles to use
Other font styles liked:
- Calibri
Requirements
Must have
- Must include the BrindlewayCare brand name in it's current font
- Must include logo (3 leaves in gold circle)
- Must include Business Card Details
Nice to have
- Elements of gold
- White space
- Something autumn themed but not too cliched
Should not have
- No blue - used by a major competitor and we would like to differentiate from them
- Large blocks of dark green colour (the green that appears in our leaves on the logo on our current business card is the background colour and it is far too dark)

```html
<!DOCTYPE html>
<html lang="en">
<head>
<meta charset="utf-8">
<title>BrindlewayCare – Business Card</title>
<link rel="stylesheet" href="https://fonts.googleapis.com/css2?family=Open+Sans:wght@300;400;700&display=swap">
<style>
  :root {
    --page: #ece6dc;
    --green: #5d9a3a;
    --green-light: #7cb552;
    --green-dark: #4a852c;
    --yellow: #c9c23e;
    --yellow-light: #d8d356;
    --red: #c8284f;
    --cream: #e9dcc0;
    --gold: #c9a85a;
    --white: #ffffff;
  }
  html, body {
    margin: 0;
    width: 1200px;
    height: 1022px;
    overflow: hidden;
    background: var(--page);
    font-family: "Open Sans", Calibri, sans-serif;
  }
  .sheet {
    position: relative;
    width: 1200px;
    height: 1022px;
  }
  .card {
    position: absolute;
    left: 200px;
    width: 800px;
    height: 457px;
    border-radius: 14px;
    overflow: hidden;
    box-shadow: 0 6px 18px rgba(0,0,0,0.18);
  }
  .card--front { top: 40px; }
  .card--back  { top: 525px; }
  .card__art {
    position: absolute;
    inset: 0;
    width: 100%;
    height: 100%;
  }
  .contact {
    position: absolute;
    left: 52px;
    top: 70px;
    color: var(--white);
  }
  .contact__name {
    margin: 0;
    font-size: 27px;
    font-weight: 700;
    letter-spacing: 0.5px;
    text-transform: uppercase;
  }
  .contact__title {
    margin: 2px 0 22px;
    font-size: 17px;
    color: var(--red);
  }
  .contact__line {
    display: flex;
    align-items: center;
    gap: 10px;
    margin: 4px 0;
    font-size: 17px;
  }
  .contact__icon { width: 16px; height: 16px; flex: none; }
  .locations {
    position: absolute;
    left: 52px;
    top: 268px;
    margin: 0;
    color: var(--white);
    font-size: 18px;
    line-height: 1.45;
  }
  .brand {
    position: absolute;
    display: flex;
    align-items: center;
    gap: 16px;
  }
  .brand__mark {
    border-radius: 50%;
    background: var(--cream);
    border: 3px solid var(--gold);
    flex: none;
  }
  .brand__name {
    font-weight: 300;
    color: var(--white);
    letter-spacing: 0.5px;
  }
  .card--front .brand { left: 380px; top: 70px; }
  .card--front .brand__mark { width: 76px; height: 76px; }
  .card--front .brand__name { font-size: 40px; }
  .card--back .brand { left: 330px; top: 180px; }
  .card--back .brand__mark { width: 90px; height: 90px; }
  .card--back .brand__name { font-size: 46px; }
</style>
</head>
<body>
<main class="sheet">

  <section class="card card--front" aria-label="Business card front">
    <svg class="card__art" viewBox="0 0 800 457" preserveAspectRatio="none" aria-hidden="true">
      <defs>
        <linearGradient id="frontGreen" x1="0" y1="0" x2="1" y2="1">
          <stop offset="0" stop-color="var(--green-light)"/>
          <stop offset="1" stop-color="var(--green-dark)"/>
        </linearGradient>
        <linearGradient id="frontYellow" x1="0" y1="0" x2="1" y2="1">
          <stop offset="0" stop-color="var(--yellow-light)"/>
          <stop offset="1" stop-color="var(--yellow)"/>
        </linearGradient>
      </defs>
      <rect width="800" height="457" fill="url(#frontGreen)"/>
      <path class="swoosh-red" d="M330 457 C540 412 705 250 800 20 L800 60 C720 260 560 420 385 457 Z" fill="var(--red)"/>
      <path class="swoosh-yellow" d="M385 457 C560 420 720 260 800 60 L800 457 Z" fill="url(#frontYellow)"/>
    </svg>

    <div class="brand">
      <span class="brand__mark"></span>
    </div>
    <div class="brand" style="left:380px; top:165px;">
      <span class="brand__name" style="font-size:40px;">BrindlewayCare</span>
    </div>

    <div class="contact">
      <h1 class="contact__name">Derek Mallow</h1>
      <p class="contact__title">Executive Chairman</p>
      <p class="contact__line">
        <svg class="contact__icon" viewBox="0 0 16 16" aria-hidden="true">
          <path d="M4 1 L6.5 4.5 L5 6.5 C6 8.5 7.5 10 9.5 11 L11.5 9.5 L15 12 L13 15 C7 14.5 1.5 9 1 3 Z" fill="var(--red)"/>
        </svg>
        <span>01742 918576</span>
      </p>
      <p class="contact__line">
        <svg class="contact__icon" viewBox="0 0 16 16" aria-hidden="true">
          <rect x="1" y="3" width="14" height="10" fill="none" stroke="var(--red)" stroke-width="1.6"/>
          <path d="M1 3 L8 9 L15 3" fill="none" stroke="var(--red)" stroke-width="1.6"/>
        </svg>
        <span>d.mallow@plumvora.example</span>
      </p>
    </div>

    <p class="locations">United Kingdom<br>Australia, New Zealand</p>
  </section>

  <section class="card card--back" aria-label="Business card back">
    <svg class="card__art" viewBox="0 0 800 457" preserveAspectRatio="none" aria-hidden="true">
      <defs>
        <linearGradient id="backGreen" x1="0" y1="0" x2="1" y2="1">
          <stop offset="0" stop-color="var(--green-light)"/>
          <stop offset="1" stop-color="var(--green-dark)"/>
        </linearGradient>
      </defs>
      <rect width="800" height="457" fill="url(#backGreen)"/>
      <path class="band-yellow" d="M0 120 C90 200 170 330 230 457 L0 457 Z" fill="var(--yellow)"/>
    </svg>
    <div class="brand">
      <span class="brand__mark"></span>
      <span class="brand__name">BrindlewayCare</span>
    </div>
  </section>

</main>
</body>
</html>
```